New webdesign for a cable company

We need a new design for Lunor Media.

There exist a suggestion for the page, were we have attached files to show you this. The design here is not good enough, but here you can se what content we need.

You can feel free to give adjustment to this design to make it better, our blow us away with a new brilliant design, but from this design you see what content we need.

The important is that the company get a design who represent its products:
- TV = Cable TV
- Bredbånd = Broadband
- Mobil = Mobile phone
- Strøm = Electricity
- Alarm = Alarm
- Lunor Komplett = a cobain pagage of all our products.

Lunor Media would like costumers who visit the site to het the impression that Lunor Media is a professional, innovative and fun company.
Updates

We have to day uploaded pictures of the existing page as the link haven't been working for the most of you as it's placed on a server our developer are using and is often shut it down. 

We have also updated the brief with some new and updated description so please read true the updated brief. 

We will at the same time inform that we haven't been able to give feedback on any of the received design and are sorry for that, we will within the next 24 hours hopefully have started responded the different received designs.

Looking forward to see more suggestion and hope you will help us create and very professional and informative design. 

Reason: We have decided to extend the deadline due to the number of design suggestion who is sent in and your lack of response to all designers due to our own workload.

This project was unfortunately for different reason put on ice for a while, but we are now ready to complete the design and will answer and give feedback too all the received design suggestions. 

Within a couple of days we hope we have answered all you who sent us suggestions, we appreciate all suggestions and hope to get in more suggestions.

Reason: Deisgn description have been updated

Target Market(s)

Our costumer are both private and companies

Industry/Entity Type

Tv

Requirements
Must have
• A easy way to promote and inform about changes in our products, there are a constant change in our products and it must bee a easy and good way to changes ass the marked change. Cheek out this link, for a example of what we like/think of here, https://nett.fjordsignal.no

On all pages there must be a easy way to click on a order button and too inform about your interest (thats two different things), could be placed in the top right corner for example. In the order form you should follow a step by step part:
1. Cheek what product we can provide you.
2. Chooce products.
3. Costumer inforamtion.
4. Confirmation.

Somewere on the portal it must be possible for costumers to log on to their own administration, where they can cheek for invoices, other statuses, etc.

A main menu existing of:
Hjem (Home)
Produkter (Products)
Storkunde (key account/large costumers)
Kundeservice (Costumerservice)
Min side (My page)

The main menu should have the following sub titles:
- Under "Produkter"/products our different products must be listed
- Under "Kundeservice"/Costumerservice it must have these submenus:
- Hjelp og støtte = Help.
- Faktura = Invoice
- Brukerguider = Userguides
- Abbonementavtaler = Terms and conditions.

A bottom menu where we have 5 main categories, with sub categories:
Om oss (about us)
- Om Lunor Media (about Lunor Media)
- Kontaktinformajson ( contact information)
- Pressemeldinger (Pressrelese)
- Ledige stillinger (positions available)
- KRAV ( and organisastion in our field)

Produkter (Product)
- TV (TV)
- Bredbånd (Broadand)
- Telefoni (telephony, both mobil)
- Strøm (elecricity)
- Arlam (Alarm)

Borrettslag/Sameier (Housing cooperatives)
- Løsninger (solutions)
- Produkter (product)
- Kontaktpersoner (contactpersons)

Utbygger (developer)
- Hva vi kan gjøre for dere. (What we can do for you)

Opperatørnett (operators)

Build up the categories and bottom menu something like this:
https://nett.fjordsignal.no
www.brevix.com
Nice to have
• A main menu existing of:
Hjem (Home)
Produkter (Products)
Lunor Media
Kontakt oss (Contact us)

Under "Produkter"/products our different products must be listed and under "Kundeservice"/Costumerservice it must have these submenus:
- Hjelp og støtte = Help.
- Faktura = Invoice
Should not have
• Any translation section since the homepage only will be in Norwegian.

```html
<!DOCTYPE html>
<html lang="no">
<head>
<meta charset="utf-8">
<title>Lunor Media – Produkter</title>
<link rel="stylesheet" href="https://fonts.googleapis.com/css2?family=Open+Sans:wght@400;600;700;800&family=Arimo:wght@400&display=swap">
<style>
:root{
  --blue:#1a58c4;
  --blue-dark:#0c4cb5;
  --blue-light:#2d86e6;
  --orange:#f07c0e;
  --ink:#222;
  --muted:#555;
  --panel:#e8edf2;
  --panel-line:#cfd6de;
  --footer:#4a4a4a;
  --footer-box:#686868;
  --footer-input:#6e6e6e;
  --white:#fff;
}
*{box-sizing:border-box;margin:0;padding:0}
html,body{width:1029px;height:1200px;overflow:hidden;background:var(--white)}
body{position:relative;font-family:"Open Sans",Arial,sans-serif;color:var(--ink)}
.abs{position:absolute}
h1,h2,h3{font-weight:400}

.site-header{position:absolute;left:0;top:0;width:1029px;height:99px;background:linear-gradient(#f1f1f1,#fff 30px)}
.brand{left:135px;top:33px;display:flex;align-items:center;gap:8px;font-size:23px;font-weight:600;color:var(--blue)}
.brand-mark{width:20px;height:20px;border-radius:50%;background:var(--blue)}
.main-nav{left:330px;top:49px;display:flex;gap:12px;font-size:12px}
.main-nav .active{color:var(--orange)}
.account-bar{right:128px;top:6px;display:flex;gap:6px}
.account-bar span{height:18px;padding:0 8px;font-size:10px;line-height:17px;border:1px solid #b7bfc8;background:var(--white);color:#444}
.account-bar .interest{border-color:var(--blue);color:var(--blue)}
.account-bar .order{border-color:var(--orange);background:var(--orange);color:var(--white);font-weight:600}
.call-hours{right:132px;top:30px;font-size:10px;color:var(--muted)}
.call-number{right:128px;top:44px;font-size:19px;color:#666;display:flex;align-items:center;gap:6px}

.hero{position:absolute;left:0;top:99px;width:1029px;height:300px;background:linear-gradient(var(--blue-dark),var(--blue-light))}
.hero-title{left:146px;top:120px;font-size:38px;font-weight:600;color:var(--white)}

.content-sheet{position:absolute;left:135px;top:187px;width:774px;height:693px;background:var(--white);box-shadow:0 0 4px rgba(0,0,0,.25)}
.sub-nav{right:160px;top:198px;display:flex;gap:15px;font-size:13px}
.sub-nav .active{color:var(--blue);text-decoration:underline}
.page-title{left:174px;top:220px;font-size:34px;font-weight:800;color:var(--orange);letter-spacing:-.5px}

.card{position:absolute;top:292px;height:566px;background:var(--panel);border:1px solid var(--panel-line);border-radius:4px;box-shadow:1px 2px 3px rgba(0,0,0,.2)}
.card-form{left:175px;width:432px}
.card-contact{left:623px;width:247px}

.photo{left:195px;top:312px;width:122px;height:94px;background:linear-gradient(135deg,#8a5a3e,#c9b49a 60%,#6d6a66);border:1px solid #999}
.person-name{left:328px;top:314px;font-size:16px}
.person-bio{left:329px;top:338px;width:262px;font-family:Arimo,Arial,sans-serif;font-size:9.3px;line-height:14.5px;color:#444}

.form-title{left:193px;top:428px;font-size:26px;font-weight:400;color:var(--blue)}
.form-rule{left:193px;top:462px;width:399px;height:1px;background:#c8d4e4}
.field-label{width:90px;text-align:right;font-size:12.5px;left:193px}
.field-input{left:292px;width:192px;height:20px;background:var(--white);border:1px solid #b7bfc8}
.check-label{left:196px;top:687px;font-size:12.5px}
.check-box{left:378px;top:686px}
.area-label{left:196px;top:721px;font-size:12.5px}
.text-area{left:195px;top:741px;width:305px;height:72px;background:var(--white);border:1px solid #b7bfc8}
.submit-btn{left:400px;top:823px;width:99px;height:21px;border:1px solid #b0b7c0;background:linear-gradient(#fafafa,#e2e6ea);font-size:12.5px;color:#777;display:flex;align-items:center;justify-content:center;gap:6px}

.contact-head{left:634px;font-size:17px;color:#333}
.contact-rule{left:634px;width:226px;height:1px;background:#d3dbe4}
.contact-phone{left:641px;top:348px;font-size:26px;color:var(--blue)}
.contact-note{left:644px;top:382px;font-size:10px}
.contact-mail{left:634px;top:447px;font-size:17px;color:var(--blue);text-decoration:underline}

.site-footer{position:absolute;left:0;top:880px;width:1029px;height:320px;background:var(--footer);color:var(--white)}
.foot-head{font-size:16px;top:896px;color:var(--white)}
.foot-rule{height:1px;background:#6a6a6a;top:926px}
.foot-item{left:169px;font-size:10.5px;line-height:14.5px;color:#eee}
.foot-icon{left:149px}
.stream-box{left:388px;top:930px;width:270px;height:130px;background:var(--footer-box)}
.stream-item{left:414px;width:218px;font-family:Arimo,Arial,sans-serif;font-size:8.5px;line-height:10.5px;color:#eee}
.stream-date{right:400px;font-family:Arimo,Arial,sans-serif;font-size:8.5px;color:#eee}
.stream-rule{left:400px;width:243px;height:1px;background:#888}
.sub-label{font-family:Arimo,Arial,sans-serif;font-size:9.5px;color:#eee}
.sub-input{left:749px;width:150px;height:21px;background:var(--footer-input)}
.sub-btn{left:749px;top:1006px;width:87px;height:21px;background:var(--orange);border:1px solid #ffb069;font-size:12px;color:var(--white);display:flex;align-items:center;justify-content:center}

.category-menu{left:147px;top:1080px;display:flex;gap:0}
.category{width:155px}
.category h4{font-size:11.5px;font-weight:600;color:var(--white);margin-bottom:3px}
.category li{list-style:none;font-family:Arimo,Arial,sans-serif;font-size:9.5px;line-height:12.5px;color:#ccc}
.legal{top:1182px;font-family:Arimo,Arial,sans-serif;font-size:9.5px;color:#bbb}
</style>
</head>
<body>

<header class="site-header">
  <div class="abs brand"><span class="brand-mark"></span>Lunor Media</div>
  <nav class="abs main-nav">
    <span>Hjem</span><span class="active">Produkter</span><span>Storkunde</span><span>Kundeservice</span><span>Min side</span><span>Om oss</span><span>Kontakt oss</span>
  </nav>
  <div class="abs account-bar"><span>Logg inn</span><span class="interest">Meld interesse</span><span class="order">Bestill</span></div>
  <div class="abs call-hours">Ring oss hverdager 10:00 - 15:00</div>
  <div class="abs call-number">
    <svg width="10" height="18" viewBox="0 0 10 18"><path d="M7 1 3 2C1 6 1 12 3 16l4 1 1-4-3-1c-.6-2-.6-4 0-6l3-1z" fill="#f07c0e"/></svg>
    44 12 34 56
  </div>
</header>

<section class="hero"></section>
<h1 class="abs hero-title">Produkter</h1>

<main class="content-sheet"></main>
<nav class="abs sub-nav"><span>TV</span><span>Bredband</span><span>Mobil</span><span class="active">Strom</span><span>Lunor Komplett</span></nav>
<h2 class="abs page-title">Mobilabonnement</h2>

<section class="card card-form"></section>
<div class="abs photo" role="img" aria-label="Foto av kundekontakt med mobiltelefon"></div>
<div class="abs person-name">Mira Solberg</div>
<p class="abs person-bio">Lorem ipsum dolor sit amet, consectetur adipisicing elitLorem ipsum dolor.Lorem ipsum dolor sit amet, con-sectetur adipisicing elitLorem ipsum dolor. Lorem ipsum dolor sit amet, consectetur adipisicing elitLorem ipsum dolor.</p>

<h3 class="abs form-title">Meld Interesse</h3>
<div class="abs form-rule"></div>

<div class="abs field-label" style="top:480px">Kundenummer</div><div class="abs field-input" style="top:478px"></div>
<div class="abs field-label" style="top:505px">Fornavn</div><div class="abs field-input" style="top:503px"></div>
<div class="abs field-label" style="top:530px">Adresse</div><div class="abs field-input" style="top:528px"></div>
<div class="abs field-label" style="top:555px">Postnummer</div><div class="abs field-input" style="top:553px"></div>
<div class="abs field-label" style="top:579px">Telefon</div><div class="abs field-input" style="top:577px"></div>
<div class="abs field-label" style="top:604px">Etternavn</div><div class="abs field-input" style="top:602px"></div>
<div class="abs field-label" style="top:629px">Poststed</div><div class="abs field-input" style="top:627px"></div>
<div class="abs field-label" style="top:654px">E-post</div><div class="abs field-input" style="top:652px"></div>

<div class="abs check-label">Jeg er interessert i bredband?</div>
<svg class="abs check-box" width="28" height="24" viewBox="0 0 28 24">
  <rect x="1" y="5" width="17" height="17" fill="#fff" stroke="#1a58c4" stroke-width="2"/>
  <path d="M5 13l5 5L26 2" fill="none" stroke="#1a58c4" stroke-width="4"/>
</svg>
<div class="abs area-label">Ved levering ab bredband, hva er viktig for deg?</div>
<div class="abs text-area"></div>
<div class="abs submit-btn">Sind skjema
  <svg width="8" height="11" viewBox="0 0 8 11"><path d="M1 1l5 4.5L1 10" fill="none" stroke="#555" stroke-width="2"/></svg>
</div>

<aside class="card card-contact"></aside>
<div class="abs contact-head" style="top:316px">Telefon:</div>
<div class="abs contact-rule" style="top:345px"></div>
<div class="abs contact-phone">4 12 34 56</div>
<div class="abs contact-note">Telefon betjent hverdager 10:00 -15:00</div>
<div class="abs contact-head" style="top:423px">E-post:</div>
<div class="abs contact-mail">post@lunormedia.no</div>
<div class="abs contact-rule" style="top:834px"></div>

<footer class="site-footer"></footer>
<div class="abs foot-head" style="left:147px">Kontakt oss</div>
<div class="abs foot-rule" style="left:147px;width:199px"></div>
<svg class="abs foot-icon" style="top:946px" width="12" height="16" viewBox="0 0 12 16"><path d="M6 0a6 6 0 0 0-6 6c0 4 6 10 6 10s6-6 6-10a6 6 0 0 0-6-6zm0 8.5A2.5 2.5 0 1 1 6 3.5a2.5 2.5 0 0 1 0 5z" fill="#fff"/></svg>
<div class="abs foot-item" style="top:939px;width:200px">Lorem ipsum dolor sit amet, consectetur adipisicing elit, sed do eiusmod tempor eiusmod tempor</div>
<svg class="abs foot-icon" style="top:994px" width="10" height="16" viewBox="0 0 10 18"><path d="M7 1 3 2C1 6 1 12 3 16l4 1 1-4-3-1c-.6-2-.6-4 0-6l3-1z" fill="#fff"/></svg>
<div class="abs foot-item" style="top:994px">44 12 34 56</div>
<svg class="abs foot-icon" style="top:1024px" width="16" height="12" viewBox="0 0 16 12"><rect x="0" y="0" width="16" height="12" fill="#fff"/><path d="M0 0l8 7 8-7" fill="none" stroke="#4a4a4a" stroke-width="1.5"/></svg>
<div class="abs foot-item" style="top:1022px">post@lunormedia.no</div>

<svg class="abs" style="left:418px;top:917px" width="34" height="14" viewBox="0 0 34 14"><path d="M34 0 0 14h34z" fill="#686868"/></svg>
<div class="abs" style="left:464px;top:902px;width:16px;height:16px;border-radius:50%;background:var(--orange)"></div>
<div class="abs foot-head" style="left:491px;font-size:14px;top:900px">Kvitter Stream</div>
<div class="abs stream-box"></div>
<div class="abs stream-item" style="top:939px">Lorem ipsum dolor sit amet, consectetur adipisicing elit, sed do eiusmod tempor</div>
<div class="abs stream-date" style="top:959px">07,May 2013</div>
<div class="abs stream-rule" style="top:975px"></div>
<div class="abs stream-item" style="top:981px">Lorem ipsum dolor sit amet, consectetur adipisicing elit, sed do eiusmod tempor</div>
<div class="abs stream-date" style="top:1001px">07,May 2013</div>
<div class="abs stream-rule" style="top:1017px"></div>
<div class="abs stream-item" style="top:1023px">Lorem ipsum dolor sit amet, consectetur adipisicing elit, sed do eiusmod tempor</div>
<div class="abs stream-date" style="top:1043px">07,May 2013</div>

<div class="abs foot-head" style="left:712px">Subscribe</div>
<div class="abs foot-rule" style="left:712px;width:197px"></div>
<div class="abs sub-label" style="left:711px;top:944px">Name:</div>
<div class="abs sub-input" style="top:938px"></div>
<div class="abs sub-label" style="left:712px;top:977px">Email:</div>
<div class="abs sub-input" style="top:971px"></div>
<div class="abs sub-btn">Subscribe &nbsp;&gt;</div>

<div class="abs" style="left:137px;top:1070px;width:772px;height:1px;background:#5e5e5e"></div>
<nav class="abs category-menu">
  <div class="category"><h4>Om oss</h4><ul><li>Om Lunor Media</li><li>Kontaktinformasjon</li><li>Pressemeldinger</li><li>Ledige stillinger</li><li>KRAV</li></ul></div>
  <div class="category"><h4>Produkter</h4><ul><li>TV</li><li>Bredbånd</li><li>Telefoni</li><li>Strøm</li><li>Alarm</li></ul></div>
  <div class="category" style="width:185px"><h4>Borettslag/Sameier</h4><ul><li>Løsninger</li><li>Produkter</li><li>Kontaktpersoner</li></ul></div>
  <div class="category"><h4>Utbygger</h4><ul><li>Hva vi kan gjøre for dere</li></ul></div>
  <div class="category" style="width:120px"><h4>Operatørnett</h4></div>
</nav>

<div class="abs" style="left:137px;top:1172px;width:772px;height:1px;background:#5e5e5e"></div>
<div class="abs legal" style="left:171px">@ Copyright 2013 &nbsp;| &nbsp;Lunor Media &nbsp; All rights reserved.</div>

</body>
</html>
```